Business Cards for new orthopaedic surgery practice

My husband and I are starting our own orthopaedic surgery practice. We are looking for a business card that is uniform, but one will have my name/title and the other will have his. You can just create one design with my name on it for now. But when I choose your design as the winning design I will ask that you add another copy with his name/title.

We are looking for classy, simple, elite all in one. We like dark blues/a little gold/yellow. Something that goes with our logo. We want our logo incorporated. Here is all the info you need:
Business name: RV Bone & Vitality Center
Location: 38517 North Willowmere Ave
Maple Harbor, FL 33418
Phone: 954-218-4063
Fax: 954-582-7341
Email: info@myrvbonecare.example

Names: Lydia Vance, M.D.
Board Certified Hand and Upper Extremity Surgeon

Ebo Dansu, M.D.
Board Certified Hip & Knee Replacement/General Orthopaedic Surgeon

Can decide what you want to put on the back. Maybe a slogan:
Grounded in Care. Centered on You

I am just going to upload our logo. The only thing is if we select you as the winning design, the location, and phone numbers may change. We will need your help to update that once fully solidified.

Industry/Entity Type

Medical

Contact Information for Business Card

Colors
0054AA
0677BA
7BADD7
CADEEF
E8F1F8
0094D4
00A9DD
6FCCEA
C7EBF8
E9F6FB

Requirements
Must have
• class, appeal,
Should not have
• We want to air on the side of masculine if we are looking at masculine vs. feminine feel. But we still want it classy, sophisticated, and something we will love

```html
<!DOCTYPE html>
<html lang="en">
<head>
<meta charset="utf-8">
<title>RV Bone &amp; Vitality Center – Business Card</title>
<link href="https://fonts.googleapis.com/css2?family=Montserrat:wght@400;500;600;700&display=swap" rel="stylesheet">
<style>
  :root {
    --backdrop: #969696;
    --sky: #14bbe3;
    --sky-light: #3ccbea;
    --navy: #27388a;
    --cyan: #1bb6e0;
    --ink: #2b2b2b;
    --paper: #ffffff;
    --rule: #2f7fd0;
  }
  * { box-sizing: border-box; margin: 0; padding: 0; }
  html, body { width: 1200px; height: 1108px; overflow: hidden; }
  body {
    background: var(--backdrop);
    font-family: "Montserrat", sans-serif;
    position: relative;
  }
  .card {
    position: absolute;
    left: 242px;
    width: 715px;
    height: 409px;
  }
  .card-front {
    top: 119px;
    background: linear-gradient(120deg, var(--sky) 0%, var(--sky) 38%, var(--sky-light) 55%, var(--sky) 80%);
  }
  .card-back { top: 580px; background: var(--paper); }

  .brand {
    position: absolute;
    left: 0; right: 0;
    display: flex;
    align-items: center;
    justify-content: center;
    gap: 16px;
    color: var(--navy);
    font-weight: 600;
    white-space: nowrap;
  }
  .brand-dot { border-radius: 50%; background: var(--navy); flex: none; }
  .card-front .brand { top: 182px; font-size: 36px; }
  .card-front .brand-dot { width: 30px; height: 30px; }
  .card-back .brand { top: 66px; font-size: 22px; gap: 10px; }
  .card-back .brand-dot { width: 18px; height: 18px; }

  .tagline {
    position: absolute;
    top: 364px; left: 0; right: 0;
    text-align: center;
    color: var(--paper);
    font-size: 18px;
    font-weight: 400;
  }

  .doctor { position: absolute; left: 0; right: 0; text-align: center; }
  .doctor-name { color: var(--cyan); font-weight: 700; font-size: 31px; line-height: 1; }
  .doctor-title { color: var(--ink); font-size: 16.5px; font-weight: 500; margin-top: 8px; white-space: nowrap; }
  .doctor-one { top: 157px; }
  .doctor-two { top: 229px; }

  .contact-address {
    position: absolute;
    top: 302px; right: 369px;
    text-align: right;
    font-size: 17px;
    line-height: 27px;
    color: var(--ink);
    font-style: normal;
    white-space: nowrap;
  }
  .contact-address .office { color: var(--cyan); }
  .contact-rule {
    position: absolute;
    left: 373px; top: 308px;
    width: 2px; height: 72px;
    background: var(--rule);
  }
  .contact-lines {
    position: absolute;
    top: 302px; left: 401px;
    list-style: none;
    font-size: 17px;
    line-height: 27px;
    color: var(--ink);
    white-space: nowrap;
  }
  .contact-lines li { display: flex; align-items: center; gap: 8px; }
  .contact-lines svg { width: 16px; height: 14px; fill: var(--cyan); flex: none; }
</style>
</head>
<body>
  <section class="card card-front">
    <div class="brand"><span class="brand-dot"></span><span>RV Bone &amp; Vitality Center</span></div>
    <p class="tagline">Grounded in Care. Centered on You</p>
  </section>

  <section class="card card-back">
    <div class="brand"><span class="brand-dot"></span><span>RV Bone &amp; Vitality Center</span></div>

    <div class="doctor doctor-one">
      <h2 class="doctor-name">Lydia Vance, M.D.</h2>
      <p class="doctor-title">Board Certified Hand and Upper Extremity Surgeon</p>
    </div>
    <div class="doctor doctor-two">
      <h2 class="doctor-name">Ebo Dansu, M.D.</h2>
      <p class="doctor-title">Board Certified Hip &amp; Knee Replacement/General Orthopaedic Surgeon</p>
    </div>

    <address class="contact-address">
      <span class="office">RV Orthopaedic Specialists</span><br>
      38517 North Willowmere Ave<br>
      Maple Harbor, FL 33418
    </address>
    <div class="contact-rule"></div>
    <ul class="contact-lines">
      <li>
        <svg viewBox="0 0 16 14" aria-hidden="true"><path d="M1 5c0-3 3-4 7-4s7 1 7 4l-3 1-1-2H5L4 6zM3 7l2-2h6l2 2v6H3z"/></svg>
        954-218-4063
      </li>
      <li>
        <svg viewBox="0 0 16 14" aria-hidden="true"><path d="M4 0h8v4H4zM1 5h14v6h-3V8H4v3H1zM5 9h6v5H5z"/></svg>
        954-582-7341
      </li>
      <li>
        <svg viewBox="0 0 16 14" aria-hidden="true"><path d="M1 2h14v1L8 8 1 3zM1 5l7 5 7-5v7H1z"/></svg>
        info@myrvbonecare.example
      </li>
    </ul>
  </section>
</body>
</html>
```